Redesign Of Current Landing Page

I need to redesign this landing page https://www.brightlanepromo.biz/?page=landing&landing=23 (Please do not opt in because when you do it will show you the home page. Please clear your cookies before going to this url above to view the 1 page landing page.)

Please use my updated website as a reference for colors and logo.
http://sitecradlewerk.com/dh/bpq/index.html

I would like the call to action to be a button that opens into a lead form...

Button would be "Download Samples"

Target Market(s)

small business owners

Industry/Entity Type

Marketing

Number of Pages Required

1 page

Colors

Designer to choose colors to be used in the design.

Requirements
Must have
• must be full responsive on all devices
Nice to have
• must have a legitimate professional apeal to it
Should not have
• open

```html
<!DOCTYPE html>
<html lang="en">
<head>
<meta charset="utf-8">
<title>Brightlane Promo Incentives – Attract More Customers</title>
<link href="https://fonts.googleapis.com/css2?family=Lato:ital,wght@0,300;0,400;0,700;0,900;1,400&display=swap" rel="stylesheet">
<style>
  :root {
    --ink-dark: #1b1b1b;
    --page-grey: #e2e2e2;
    --body-text: #4f4f4f;
    --accent-red: #e31b23;
    --brand-blue: #1c74c4;
    --cta-yellow: #f8b60f;
    --white: #ffffff;
    --icon-grey: #3a3a3a;
  }
  * { box-sizing: border-box; margin: 0; padding: 0; }
  html, body { width: 1200px; height: 2769px; overflow: hidden; }
  body {
    position: relative;
    background: var(--page-grey);
    font-family: "Lato", Arial, sans-serif;
    color: var(--body-text);
  }

  /* Header */
  .site-header {
    position: absolute; left: 0; top: 0; width: 1200px; height: 126px;
    background: var(--ink-dark);
  }
  .brand {
    position: absolute; left: 101px; top: 42px;
    display: flex; align-items: center; gap: 14px;
  }
  .brand-square { width: 36px; height: 36px; background: var(--brand-blue); }
  .brand-name {
    font-weight: 700; font-size: 30px; letter-spacing: 1px;
    color: var(--brand-blue); text-transform: uppercase;
  }
  .header-contact {
    position: absolute; right: 98px; top: 30px; text-align: right; color: var(--white);
  }
  .header-phone { font-size: 32px; font-weight: 400; line-height: 1.1; letter-spacing: .5px; }
  .header-hours { font-size: 15px; font-weight: 700; margin-top: 2px; }

  /* Hero */
  .hero-photo {
    position: absolute; left: 0; top: 126px; width: 1200px; height: 627px;
    background:
      radial-gradient(ellipse 340px 420px at 830px 300px, rgba(120,150,175,.55), transparent 70%),
      radial-gradient(circle 120px at 1000px 110px, rgba(255,220,160,.55), transparent 70%),
      linear-gradient(100deg, #2d4452 0%, #4d6674 32%, #6e8b99 55%, #3a5466 78%, #243542 100%);
  }
  .hero-copy { position: absolute; left: 100px; top: 274px; color: var(--white); }
  .hero-title {
    font-size: 45px; font-weight: 700; letter-spacing: 3px; line-height: 48px;
    text-transform: uppercase;
  }
  .hero-sub {
    margin-top: 20px; font-size: 17px; font-weight: 700; letter-spacing: 1px;
    line-height: 31.5px; text-transform: uppercase;
  }

  /* Lead form */
  .form-label-bar {
    position: absolute; left: 100px; top: 698px; width: 1002px; height: 55px;
    background: rgba(20,20,20,.82);
    color: var(--white); font-size: 24px; font-weight: 700; letter-spacing: 1.5px;
    padding: 13px 0 0 59px;
  }
  .lead-form {
    position: absolute; left: 100px; top: 753px; width: 1002px; height: 164px;
    background: var(--brand-blue); color: var(--white);
  }
  .lead-intro {
    position: absolute; left: 59px; top: 10px; width: 820px;
    font-size: 22px; line-height: 25px; letter-spacing: .5px;
  }
  .lead-field {
    position: absolute; top: 76px; width: 173px; height: 44px;
    border: 1.5px solid rgba(255,255,255,.75); background: rgba(255,255,255,.08);
    color: var(--white); font-size: 14px; font-weight: 700; padding: 14px 0 0 14px;
  }
  .lead-field.name { left: 59px; }
  .lead-field.email { left: 277px; }
  .lead-field.phone { left: 489px; }
  .download-button {
    position: absolute; left: 685px; top: 76px; width: 256px; height: 44px;
    background: var(--cta-yellow); color: var(--ink-dark);
    text-align: center; font-weight: 900; text-transform: uppercase;
    font-size: 13px; letter-spacing: 1px; line-height: 15px; padding-top: 6px;
  }
  .download-button small { display: block; font-size: 11px; font-weight: 700; }
  .mandatory-note {
    position: absolute; left: 59px; top: 134px;
    font-size: 14px; font-style: italic; font-weight: 700;
  }

  /* Content sections */
  .section-heading {
    position: absolute; left: 160px;
    font-size: 45px; font-weight: 300; letter-spacing: 2px; color: var(--accent-red);
    text-transform: uppercase; line-height: 1;
  }
  .section-text {
    position: absolute; left: 160px; width: 884px;
    font-size: 21.5px; text-align: justify; letter-spacing: .4px;
  }
  .section-text p { margin: 0; }
  .imagine-text { top: 1021px; line-height: 31px; }
  .how-text { top: 1384px; line-height: 39px; }
  .get-button {
    position: absolute; left: 870px; width: 173px; height: 32px;
    background: var(--cta-yellow); color: var(--white);
    font-size: 15px; font-weight: 900; letter-spacing: 1px;
    text-align: center; line-height: 32px; text-transform: uppercase;
  }

  .why-heading {
    position: absolute; left: 157px; top: 1768px;
    font-size: 31px; font-weight: 700; letter-spacing: 1.5px; color: var(--accent-red);
    text-transform: uppercase;
  }
  .benefit {
    position: absolute; width: 220px; margin-left: -110px; text-align: center;
    font-size: 18px; line-height: 24px; letter-spacing: .5px; color: var(--body-text);
  }
  .benefit svg { display: block; margin: 0 auto; fill: var(--icon-grey); }
  .benefit-label { display: block; }

  /* Testimonial */
  .testimonial { position: absolute; left: 148px; top: 2298px; width: 860px; }
  .quote-mark { position: absolute; left: 0; top: 0; }
  .testimonial-text {
    position: absolute; left: 51px; top: 6px; width: 806px;
    font-size: 17.5px; font-style: italic; line-height: 33.5px; letter-spacing: .4px;
    color: var(--body-text);
  }
  .testimonial-author {
    position: absolute; right: 8px; top: 214px; text-align: right;
    font-size: 18px; font-weight: 700; line-height: 32px; letter-spacing: 1px; color: #333;
  }

  /* Footer */
  .site-footer {
    position: absolute; left: 0; top: 2713px; width: 1200px; height: 56px;
    background: var(--ink-dark); color: var(--white);
    text-align: center; font-size: 18px; line-height: 56px; letter-spacing: .5px;
  }
</style>
</head>
<body>

<header class="site-header">
  <div class="brand">
    <span class="brand-square"></span>
    <span class="brand-name">Brightlane Promo Incentives</span>
  </div>
  <div class="header-contact">
    <div class="header-phone">1-800-555-0142</div>
    <div class="header-hours">Mon-Fri 8am-5pm PST</div>
  </div>
</header>

<div class="hero-photo" role="img" aria-label="Photo of a relaxed smiling businessman leaning back with hands behind his head in a bright office"></div>
<div class="hero-copy">
  <h1 class="hero-title">Attract More<br>Customers</h1>
  <p class="hero-sub">Who spend more money with<br>your business more often using<br>free vacation &amp; cruise certificates<br>and other incentives without<br>breaking the bank!</p>
</div>

<div class="form-label-bar">ENTER YOUR INFO</div>
<form class="lead-form">
  <p class="lead-intro">To be fowarded to our website for all the details and to receive samples in your email!</p>
  <div class="lead-field name">Name*</div>
  <div class="lead-field email">Email*</div>
  <div class="lead-field phone">Phone*</div>
  <div class="download-button">Download Free Samples<small>of our incentives</small></div>
  <p class="mandatory-note">*mandatory fields</p>
</form>

<h2 class="section-heading" style="top:975px">Imagine</h2>
<div class="section-text imagine-text">
  <p>being able to create exciting give away promotions that will boost your sales without ever having to worry about cost.</p>
  <p>Brightlane Promo Group, Inc. provides high-perceived value promotional incentives to businesses that want to advertise an exciting Give Away that will instantly attract more customers from your existing advertising efforts.</p>
  <p>Your business can give away incentive certificates that are redeemable for luxury hotel &amp; resort stays with airfare included, cruises, cash for gas, groceries, dining and even electronic goods.</p>
</div>
<div class="get-button" style="top:1266px">Get Incentives</div>

<h2 class="section-heading" style="top:1340px">How can we do it?</h2>
<div class="section-text how-text">
  <p>We help fill empty rooms for thousands of hotels and resorts in hundreds of destinations around the world as well as the major cruise lines. Hotels and resorts are rarely full so when we place someone in their empty rooms, they end up making it up when travelers spend money on room service, spa services, eat at their in-house restaurants, casino and take advantage of other amenities that drive revenue.</p>
  <p>We also help over 18,000 restaurants, electronic manufacturers, the major gas companies and top grocery chains in the U.S and Canada increase brand awareness as well as increase customer loyalty.</p>
</div>
<div class="get-button" style="top:1676px">Get Incentives</div>

<h2 class="why-heading">Why offer incentives to customers?</h2>

<div class="benefit" style="left:253px; top:1848px">
  <svg width="66" height="80" viewBox="0 0 66 80" aria-hidden="true">
    <rect x="2" y="58" width="10" height="20"/><rect x="18" y="46" width="10" height="32"/>
    <rect x="34" y="34" width="10" height="44"/><rect x="50" y="20" width="10" height="58"/>
    <path d="M2 40 L46 6 L42 2 L62 0 L58 18 L54 12 L6 46 Z"/>
  </svg>
  <span class="benefit-label" style="margin-top:34px">Increase Responses<br>From Your Existing Ads</span>
</div>

<div class="benefit" style="left:484px; top:1848px">
  <svg width="80" height="80" viewBox="0 0 80 80" aria-hidden="true">
    <path d="M34 2h12l2 10 8 3 8-6 8 8-6 8 3 8 10 2v12l-10 2-3 8 6 8-8 8-8-6-8 3-2 10H34l-2-10-8-3-8 6-8-8 6-8-3-8-10-2V34l10-2 3-8-6-8 8-8 8 6 8-3z M40 24a16 16 0 1 0 0.1 0z" fill-rule="evenodd"/>
    <path d="M34 36 l28 28 a5 5 0 0 1 -7 7 l-28 -28z"/>
  </svg>
  <span class="benefit-label" style="margin-top:34px">#1 Sales Closing Tool -<br>Gift w/ Purchase</span>
</div>

<div class="benefit" style="left:711px; top:1848px">
  <svg width="84" height="80" viewBox="0 0 84 80" aria-hidden="true">
    <polygon points="42,12 50,34 74,34 55,48 62,72 42,58 22,72 29,48 10,34 34,34"/>
    <polygon points="42,0 44,5 49,5 45,8 47,13 42,10 37,13 39,8 35,5 40,5"/>
    <polygon points="18,6 20,11 25,11 21,14 23,19 18,16 13,19 15,14 11,11 16,11"/>
    <polygon points="66,6 68,11 73,11 69,14 71,19 66,16 61,19 63,14 59,11 64,11"/>
    <polygon points="6,40 8,45 13,45 9,48 11,53 6,50 1,53 3,48 -1,45 4,45"/>
    <polygon points="78,40 80,45 85,45 81,48 83,53 78,50 73,53 75,48 71,45 76,45"/>
  </svg>
  <span class="benefit-label" style="margin-top:34px">Build Brand Awareness<br>and Trust</span>
</div>

<div class="benefit" style="left:945px; top:1848px">
  <svg width="80" height="80" viewBox="0 0 80 80" aria-hidden="true">
    <circle cx="14" cy="8" r="7"/><rect x="6" y="18" width="16" height="34" rx="3"/>
    <rect x="7" y="52" width="6" height="26"/><rect x="15" y="52" width="6" height="26"/>
    <circle cx="66" cy="8" r="7"/><rect x="58" y="18" width="16" height="34" rx="3"/>
    <rect x="59" y="52" width="6" height="26"/><rect x="67" y="52" width="6" height="26"/>
    <path d="M22 24 L40 34 L58 24 L58 30 L40 40 L22 30z"/>
    <rect x="44" y="42" width="20" height="16"/>
  </svg>
  <span class="benefit-label" style="margin-top:34px">Build Brand Awareness<br>and Trust</span>
</div>

<div class="benefit" style="left:480px; top:2050px">
  <svg width="80" height="64" viewBox="0 0 80 64" aria-hidden="true">
    <polygon points="30,0 30,10 80,10 80,26 30,26 30,36 0,18"/>
    <polygon points="50,28 50,38 0,38 0,54 50,54 50,64 80,46"/>
  </svg>
  <span class="benefit-label" style="margin-top:32px">Boost Repeat and Referral<br>Business-</span>
</div>

<div class="benefit" style="left:711px; top:2048px">
  <svg width="70" height="70" viewBox="0 0 80 80" aria-hidden="true">
    <path d="M34 2h12l2 10 8 3 8-6 8 8-6 8 3 8 10 2v12l-10 2-3 8 6 8-8 8-8-6-8 3-2 10H34l-2-10-8-3-8 6-8-8 6-8-3-8-10-2V34l10-2 3-8-6-8 8-8 8 6 8-3z M40 18a22 22 0 1 0 0.1 0z" fill-rule="evenodd"/>
    <text x="40" y="52" text-anchor="middle" font-family="Lato, Arial, sans-serif" font-size="32" font-weight="900">$</text>
  </svg>
  <span class="benefit-label" style="margin-top:30px">Improve Retention<br>Rates</span>
</div>

<div class="get-button" style="top:2215px">Get Incentives</div>

<blockquote class="testimonial">
  <svg class="quote-mark" width="42" height="34" viewBox="0 0 42 34" aria-hidden="true" fill="#1b1b1b">
    <path d="M0 34V20C0 9 6 2 16 0l2 5C12 7 9 11 9 16h9v18z"/>
    <path d="M22 34V20C22 9 28 2 38 0l2 5C34 7 31 11 31 16h9v18z"/>
  </svg>
  <p class="testimonial-text">I began using your incentives two years ago to boost lead generation efforts.<br>I have experienced a 63% increase in lead captures. And, even more importantly, my sales have increased as well. The ability to offer unlimited certificates and not having to pay for each certificate I give away is perhaps the best feature of the program, but having the flexibility to email or print certificates for my customers is also wonderful. I even use your html banners to automate my promotions right on my website!,</p>
  <footer class="testimonial-author">Dan R.<br>Maplewood, TN</footer>
</blockquote>

<footer class="site-footer">© 2017 Brightlane Promo Group, Inc. - All Rights Reserved</footer>

</body>
</html>
```